Wordpress Website Update - Elementor

I'm currently using Elementor and would like my site to be updated. A nice facelift to the current pages. We are a small boutique animation service company.
I have a list of similar production houses to use as references and would like the format/style of the site not to feel so corporate and infuse the fun that we bring to working with clients on animated projects.

Additionally, I'd like to add 2 more pages focusing on more portfolio work and Original IP - which is now our primary goal to sell our show ideas. Maybe have a password projected behind an image showcasing the show/ film. Go to our current site to review. www.pebblemoatfilms.com

Animation/ Commercials/ Vorlica/ Quelbar/ Durno/ KVT - Okay with first page being shorter and not as long as well. Have contact us 'above the fold' on options as well.

Animation and Film

• Current 3 pages - additional 2 - we can focus on layout and arrangement with temporary images then swap with real assets when ready.
• site examples: pirtolstudios.com, Mardle House, Fenra Studios, Gorbleck.net, Quillstone Animation, Brindlemop Animation Studios, ZaZe Studios use Varkel Plus as inspiration.

```html
<!DOCTYPE html>
<html lang="en">
<head>
<meta charset="utf-8">
<title>Pebble Moat Films – Home</title>
<link href="https://fonts.googleapis.com/css2?family=Roboto+Condensed:wght@400;700&family=Lato:wght@400;700&display=swap" rel="stylesheet">
<style>
:root{
  --red:#c8161d;
  --purple:#6b45d8;
  --purple-deep:#5a36c4;
  --ink:#111111;
  --body:#333333;
  --white:#ffffff;
  --line:#4a4a4a;
  --card-shadow:rgba(0,0,0,.12);
}
*{box-sizing:border-box;margin:0;padding:0}
html,body{width:1200px;height:4041px;overflow:hidden;background:var(--white)}
body{font-family:'Lato',sans-serif;color:var(--body)}
.page{position:relative;width:1200px;height:4041px;overflow:hidden}
.abs{position:absolute}
.cond{font-family:'Roboto Condensed',sans-serif}
.btn{position:absolute;display:flex;align-items:center;justify-content:center;gap:12px;background:var(--red);color:var(--white);font-family:'Roboto Condensed',sans-serif;font-weight:700;font-size:15px;text-transform:uppercase;border-radius:2px}
.btn svg{width:15px;height:15px}
/* hero */
.hero-photo{position:absolute;left:0;top:0;width:1200px;height:680px;background:linear-gradient(110deg,#3e3b3a 0%,#6a625b 35%,#8a7a66 60%,#a4825a 75%,#5c554f 100%)}
.hero-wave{position:absolute;left:0;top:0}
.logo{position:absolute;font-family:'Roboto Condensed',sans-serif;font-weight:700;color:var(--purple);line-height:1}
.nav{position:absolute;left:333px;top:48px;display:flex;gap:36px;font-family:'Roboto Condensed',sans-serif;font-size:15px;color:var(--white);text-transform:uppercase}
.nav .active{color:var(--red)}
.social{position:absolute;display:flex}
.social span{display:block;border:1.5px solid currentColor;border-radius:50%}
.search{position:absolute;left:916px;top:38px;width:168px;height:37px;background:var(--white);border:1px solid #ddd;display:flex;align-items:center}
.search span{flex:1;padding-left:13px;font-size:12px;color:#555}
.search i{width:34px;height:33px;margin-right:1px;background:var(--purple);display:flex;align-items:center;justify-content:center}
.hero-title{position:absolute;left:108px;top:212px;font-family:'Roboto Condensed',sans-serif;font-weight:700;font-size:45px;line-height:73px;color:var(--white);text-transform:uppercase}
/* feature rows */
.kicker{font-family:'Roboto Condensed',sans-serif;font-weight:700;font-size:14px;color:var(--ink);text-transform:uppercase}
.h2{font-family:'Roboto Condensed',sans-serif;font-weight:700;font-size:35px;color:var(--ink);text-transform:uppercase;line-height:1.1}
.copy{font-size:14.5px;line-height:26px;color:var(--body)}
.media{position:absolute;border-radius:2px}
/* bands */
.band{position:absolute;left:0;width:1200px;background:var(--purple)}
/* expertise */
.card{position:absolute;top:1900px;width:291px;height:346px;background:var(--white);box-shadow:0 2px 10px var(--card-shadow);text-align:center}
.card .icon{width:112px;height:112px;border-radius:50%;margin:42px auto 0}
.card h3{margin-top:30px;font-family:'Roboto Condensed',sans-serif;font-weight:700;font-size:15px;color:var(--ink);text-transform:uppercase}
.card p{margin:14px auto 0;width:236px;font-size:14.5px;line-height:26px}
.card .more{margin-top:10px;display:flex;justify-content:center;align-items:center;gap:10px;font-family:'Roboto Condensed',sans-serif;font-weight:700;font-size:15px;color:var(--purple)}
.arrow{position:absolute;top:2053px;width:38px;height:38px;border-radius:50%;background:var(--white);box-shadow:0 1px 6px var(--card-shadow);display:flex;align-items:center;justify-content:center}
/* projects */
.tile{position:absolute;width:311px;height:208px}
/* footer */
.foot-h{position:absolute;font-family:'Roboto Condensed',sans-serif;font-weight:700;font-size:15px;color:var(--white);text-transform:uppercase}
.foot-list{position:absolute;list-style:none;font-size:14.5px;color:var(--white)}
.foot-list li{height:30px;display:flex;align-items:center;gap:10px}
.contact-row{position:absolute;left:839px;display:flex;align-items:flex-start;gap:16px;font-size:14.5px;color:var(--white);line-height:20px}
.contact-row i{flex:none;width:32px;height:32px;border:1.5px solid var(--white);border-radius:50%;display:flex;align-items:center;justify-content:center}
</style>
</head>
<body>
<div class="page">

  <!-- HERO -->
  <div class="hero-photo" role="img" aria-label="Cosy living room with a cartoon giraffe wearing glasses beside a bookshelf"></div>
  <svg class="hero-wave" width="1200" height="680" viewBox="0 0 1200 680">
    <path d="M0,680 C140,665 250,600 360,615 C470,630 560,690 690,662 C810,636 900,515 1010,522 C1100,528 1160,590 1200,618 L1200,680 Z" fill="#ffffff"/>
  </svg>

  <div class="logo" style="left:108px;top:34px;font-size:36px">PEBBLE MOAT</div>

  <nav class="nav">
    <span class="active">Home</span><span>About Us</span><span>Projects</span><span>Contact Us</span>
  </nav>

  <div class="social" style="left:713px;top:39px;gap:12px;color:var(--white)" aria-label="Social links">
    <span style="width:34px;height:34px"></span><span style="width:34px;height:34px"></span><span style="width:34px;height:34px"></span><span style="width:34px;height:34px"></span>
  </div>

  <div class="search"><span>Search</span><i><svg width="14" height="14" viewBox="0 0 14 14"><circle cx="6" cy="6" r="4.3" fill="none" stroke="#fff" stroke-width="2"/><line x1="9.2" y1="9.2" x2="13" y2="13" stroke="#fff" stroke-width="2"/></svg></i></div>

  <h1 class="hero-title">Welcome to<br>Pebble Moat Films</h1>
  <div class="btn" style="left:108px;top:370px;width:151px;height:49px">Get Started
    <svg viewBox="0 0 16 16"><circle cx="8" cy="8" r="8" fill="#fff"/><path d="M5 8h6M8.5 5.2 11.3 8 8.5 10.8" stroke="#c8161d" stroke-width="2" fill="none"/></svg>
  </div>

  <!-- FEATURE ROW 1 -->
  <div class="abs" style="left:140px;top:776px;width:409px;text-align:right">
    <div class="kicker">Fresh out the render oven. Careful it's</div>
    <div class="h2" style="margin-top:17px">Giraffes &amp; Kids are free!</div>
    <p class="copy" style="margin-top:12px">Pebble Moat kicked major butt on this fun project. Read more about the role we played bringing this commercial to life.</p>
  </div>
  <div class="btn" style="left:400px;top:941px;width:149px;height:49px">Learn More
    <svg viewBox="0 0 16 16"><circle cx="8" cy="8" r="8" fill="#fff"/><path d="M5 8h6M8.5 5.2 11.3 8 8.5 10.8" stroke="#c8161d" stroke-width="2" fill="none"/></svg>
  </div>
  <div class="media" style="left:651px;top:756px;width:400px;height:256px;background:linear-gradient(180deg,#8a5660 0%,#7a4a4c 55%,#4e2f2c 100%)" role="img" aria-label="Dusky desert scene with a rider on a running creature"></div>

  <!-- FEATURE ROW 2 -->
  <div class="media" style="left:149px;top:1085px;width:400px;height:256px;background:linear-gradient(120deg,#4a5d86 0%,#8d8f94 45%,#b79a7d 75%,#5f5040 100%)" role="img" aria-label="Two team members smiling at a cafe table"></div>
  <div class="abs" style="left:651px;top:1075px;width:436px">
    <div class="kicker">The sky's the limit</div>
    <div class="h2" style="margin-top:17px">We make it fun</div>
    <p class="copy" style="margin-top:10px">Did we mention we LOVE what we do? The industry has changed a lot over the years. And yes there's a lot of outsourcing nowadays and you get what you pay for. So I can guarantee you get the best when you work with us. We cut the fluff and get down to business making sure it's done the right way the first time around.</p>
  </div>
  <div class="btn" style="left:651px;top:1302px;width:149px;height:49px">Learn More
    <svg viewBox="0 0 16 16"><circle cx="8" cy="8" r="8" fill="#fff"/><path d="M5 8h6M8.5 5.2 11.3 8 8.5 10.8" stroke="#c8161d" stroke-width="2" fill="none"/></svg>
  </div>

  <!-- CTA BAND -->
  <div class="band" style="top:1437px;height:279px;background:linear-gradient(90deg,#6a44d6,#6f4bdc)"></div>
  <div class="abs" style="left:180px;top:1490px;width:466px;text-align:center;color:var(--white)">
    <div class="h2" style="color:var(--white)">Why wait let's co-create!</div>
    <p style="margin-top:18px;font-size:17px">No need to scroll, save your finger and drop us a line.</p>
  </div>
  <div class="btn" style="left:339px;top:1606px;width:149px;height:49px">Contact Us
    <svg viewBox="0 0 16 16"><circle cx="8" cy="8" r="8" fill="#fff"/><path d="M5 8h6M8.5 5.2 11.3 8 8.5 10.8" stroke="#c8161d" stroke-width="2" fill="none"/></svg>
  </div>
  <div class="abs" style="left:706px;top:1455px;width:330px;height:290px;border-radius:48% 52% 40% 45%;background:linear-gradient(135deg,#8fcf3a 0%,#7ab83a 45%,#8a6be6 70%,#7c5ae0 100%)" role="img" aria-label="Two friendly cartoon monsters, one green and one purple"></div>

  <!-- EXPERTISE -->
  <div class="abs" style="left:0;top:1796px;width:1200px;text-align:center">
    <div class="kicker">Creative experts that solve problems</div>
    <div class="h2" style="margin-top:14px">Our Expertise</div>
  </div>

  <div class="arrow" style="left:41px"><svg width="12" height="14" viewBox="0 0 12 14"><path d="M8 2 3 7l5 5" stroke="#111" stroke-width="2" fill="none"/></svg></div>
  <div class="arrow" style="left:1120px"><svg width="12" height="14" viewBox="0 0 12 14"><path d="M4 2l5 5-5 5" stroke="#111" stroke-width="2" fill="none"/></svg></div>

  <div class="card" style="left:136px">
    <div class="icon" style="background:linear-gradient(135deg,#f1eef8,#f6b73c)" role="img" aria-label="Giraffe icon"></div>
    <h3>IP Creation</h3>
    <p>Developing, Directing and Selling captivating stories is in our DNA. Check what we are cooking up.</p>
    <div class="more">Read more <svg width="14" height="14" viewBox="0 0 16 16"><circle cx="8" cy="8" r="8" fill="#6b45d8"/><path d="M5 8h6M8.5 5.2 11.3 8 8.5 10.8" stroke="#fff" stroke-width="2" fill="none"/></svg></div>
  </div>
  <div class="card" style="left:455px">
    <div class="icon" style="background:linear-gradient(135deg,#f1eef8,#8fcf6a 60%,#f6d04a)" role="img" aria-label="Character with pencil icon"></div>
    <h3>Character Design</h3>
    <p>Designing premier characters from concept to finished packets for 3D Development.</p>
    <div class="more">Read more <svg width="14" height="14" viewBox="0 0 16 16"><circle cx="8" cy="8" r="8" fill="#6b45d8"/><path d="M5 8h6M8.5 5.2 11.3 8 8.5 10.8" stroke="#fff" stroke-width="2" fill="none"/></svg></div>
  </div>
  <div class="card" style="left:773px">
    <div class="icon" style="background:linear-gradient(135deg,#f1eef8,#e8404a 60%,#f6c03a)" role="img" aria-label="Castle building icon"></div>
    <h3>Vis Dev</h3>
    <p>Building worlds and settings to enrich the places characters play. Saying more with an image.</p>
    <div class="more">Read more <svg width="14" height="14" viewBox="0 0 16 16"><circle cx="8" cy="8" r="8" fill="#6b45d8"/><path d="M5 8h6M8.5 5.2 11.3 8 8.5 10.8" stroke="#fff" stroke-width="2" fill="none"/></svg></div>
  </div>

  <!-- ANIMATION REEL -->
  <div class="band" style="top:2329px;height:433px;background:linear-gradient(90deg,#6a44d6,#7450de)"></div>
  <div class="abs" style="left:108px;top:2400px;width:462px;color:var(--white)">
    <div class="h2" style="color:var(--white)">Animation Reel</div>
    <p style="margin-top:14px;font-size:14.5px;line-height:26px">Lorem ipsum dolor sit amet, consectetur adipiscing elit, sed eiusmoid tempor incididunt ut labore et dolore magna aliqua. Ut enim ad minim veniam, quis nostrud exercitation ullamco laboris nisi ut aliquip exgea commodo consequat. Duis aute irure dolor reprehenderit voluptaten velit esse cillumLorem ipsum dolor sit amet, consectetursit adipiscing elit, sed do eiusmod temporut incididunt ut labore et doloreut magna aliqua. Ut enim ad minim veniam, quis nostrud exercitation ullamcoves laboris nisi ut aliquip enim ad minim commodo consequat.</p>
  </div>
  <div class="media" style="left:634px;top:2395px;width:453px;height:303px;background:linear-gradient(90deg,#cfd2d6 0%,#b9c2cc 40%,#6f7d8c 70%,#4b3a2e 100%)" role="img" aria-label="Video still of an animated presenter scene with cartoon mascots"></div>

  <!-- PROJECTS -->
  <div class="abs h2" style="left:0;top:2835px;width:1200px;text-align:center">Our Projects</div>
  <div class="tile" style="left:111px;top:2918px;background:linear-gradient(160deg,#7aa6d8,#c9c3b8 60%,#8e8a86)" role="img" aria-label="Animated mascots marching in a parade"></div>
  <div class="tile" style="left:445px;top:2918px;background:linear-gradient(150deg,#7fb7d0,#c79a5c 55%,#5d7a3a)" role="img" aria-label="Cartoon puppy explorer"></div>
  <div class="tile" style="left:778px;top:2918px;background:linear-gradient(160deg,#2f8fd0,#1a5e9a 60%,#0f3a66)" role="img" aria-label="Underwater scene with divers and fish"></div>
  <div class="tile" style="left:111px;top:3147px;background:linear-gradient(150deg,#4e4a4a,#8a6b4a 55%,#c9b28a)" role="img" aria-label="Giraffe beside an ark painting"></div>
  <div class="tile" style="left:445px;top:3147px;background:linear-gradient(150deg,#8fb4e0,#6d9c5a 55%,#d86f9c)" role="img" aria-label="Two animated kids playing"></div>
  <div class="tile" style="left:778px;top:3147px;background:linear-gradient(150deg,#e9ecef,#5c9a4a 55%,#9a6a3a)" role="img" aria-label="Forest scene with animated creatures"></div>

  <!-- FOOTER -->
  <svg class="abs" style="left:0;top:0" width="1200" height="4041" viewBox="0 0 1200 4041">
    <path d="M0,3485 C110,3560 230,3600 340,3545 C460,3480 570,3432 710,3435 C860,3438 1010,3478 1200,3478 L1200,4041 L0,4041 Z" fill="#000000"/>
  </svg>

  <div class="foot-h" style="left:202px;top:3640px;font-size:20px">Sign up for newsletter</div>
  <div class="abs" style="left:529px;top:3630px;width:467px;height:45px;background:var(--white);border:2px solid var(--purple);display:flex;align-items:center">
    <svg style="margin-left:20px" width="15" height="12" viewBox="0 0 15 12"><rect x="1" y="1" width="13" height="10" rx="1" fill="none" stroke="#6b45d8" stroke-width="1.4"/><path d="M1 1.5 7.5 7 14 1.5" fill="none" stroke="#6b45d8" stroke-width="1.4"/></svg>
    <span style="margin-left:14px;font-size:12px;color:#555;flex:1">Enter Your Email:</span>
    <span style="width:142px;height:41px;background:var(--purple);color:var(--white);font-family:'Roboto Condensed',sans-serif;font-weight:700;font-size:15px;display:flex;align-items:center;justify-content:center">SUBMIT</span>
  </div>
  <div class="abs" style="left:111px;top:3718px;width:978px;height:1px;background:var(--line)"></div>

  <div class="logo" style="left:108px;top:3768px;font-size:34px">PEBBLE MOAT</div>
  <p class="abs" style="left:108px;top:3832px;width:240px;font-size:13px;line-height:20px;color:var(--white)">Investors, Mangers, Agents, we've got outstanding stories when it comes IP.</p>
  <div class="foot-h" style="left:108px;top:3886px">Follow us</div>
  <div class="social" style="left:108px;top:3921px;gap:9px;color:var(--white)" aria-label="Social links">
    <span style="width:31px;height:31px"></span><span style="width:31px;height:31px"></span><span style="width:31px;height:31px"></span><span style="width:31px;height:31px"></span>
  </div>

  <div class="foot-h" style="left:444px;top:3761px">Quicklinks</div>
  <ul class="foot-list" style="left:444px;top:3794px">
    <li>» Home</li><li>» About Us</li><li>» Projects</li><li>» Contact</li>
  </ul>
  <div class="foot-h" style="left:638px;top:3761px">Otherlinks</div>
  <ul class="foot-list" style="left:638px;top:3794px">
    <li>» Contact Us</li><li>» FAQ</li><li>» Services</li><li>» Privacy</li><li>» Policy</li>
  </ul>
  <div class="foot-h" style="left:839px;top:3761px">Contact us</div>
  <div class="contact-row" style="top:3802px"><i><svg width="14" height="14" viewBox="0 0 14 14"><path d="M3 1.5 5 4 4 5.5c.8 1.8 2.2 3.2 4 4L9.5 8.5 12 10.5 11 12.5C6 12.5 1.5 8 1.5 3Z" fill="none" stroke="#fff" stroke-width="1.2"/></svg></i><span style="padding-top:6px">+1 888 888 8888</span></div>
  <div class="contact-row" style="top:3860px"><i><svg width="14" height="12" viewBox="0 0 15 12"><rect x="1" y="1" width="13" height="10" rx="1" fill="none" stroke="#fff" stroke-width="1.3"/><path d="M1 1.5 7.5 7 14 1.5" fill="none" stroke="#fff" stroke-width="1.3"/></svg></i><span style="padding-top:6px">info@pebblemoatfilms.com</span></div>
  <div class="contact-row" style="top:3918px"><i><svg width="12" height="15" viewBox="0 0 12 15"><path d="M6 14C2.5 9.5 1 7.5 1 5.3a5 5 0 0 1 10 0C11 7.5 9.5 9.5 6 14Z" fill="none" stroke="#fff" stroke-width="1.3"/><circle cx="6" cy="5.3" r="1.7" fill="#fff"/></svg></i><span style="width:210px">123, Lorem ipsum dolor utd sit consectetur adipiscing ut elit.</span></div>

  <p class="abs" style="left:0;top:3998px;width:1200px;text-align:center;font-size:13px;color:var(--white)">Copyright © 2022 Pebble Moat Films All rights reserved.</p>

</div>
</body>
</html>
```